Business Card Design

New business card design

Target Market(s)

Residential & Commercial Property Managers

Industry/Entity Type

Plumbing Services

Contact Information for Business Card

Name - Rowan Keddle, title - Director, Phone Number - 0431 286 517, email - rowan@tbk-plumbing.com.au, Company ABN - 73 215 904 386,

Font styles to use
Sans Serif

Colors
0054AA
0677BA
7BADD7
CADEEF
E8F1F8

```html
<!DOCTYPE html>
<html lang="en">
<head>
<meta charset="utf-8">
<title>TBK Plumbing Services – Business Card</title>
<link rel="stylesheet" href="https://fonts.googleapis.com/css2?family=Montserrat:wght@400;500;600&display=swap">
<style>
  :root {
    --backdrop: #c4c2bd;
    --card: #1e232a;
    --accent: #0aa6e6;
    --ink-light: #f2f4f6;
    --ink-soft: #c9ced4;
    --rule: #8a9098;
  }
  * { box-sizing: border-box; margin: 0; padding: 0; }
  html, body {
    width: 1200px; height: 857px; overflow: hidden;
    background: var(--backdrop);
    font-family: "Montserrat", Arial, sans-serif;
  }
  .stage {
    position: relative; width: 1200px; height: 857px;
    display: flex; align-items: center; justify-content: center; gap: 60px;
  }
  .card {
    position: relative; width: 520px; height: 297px;
    background: var(--card);
    border-left: 4px solid var(--accent);
    border-bottom: 4px solid var(--accent);
    box-shadow: 0 14px 28px rgba(0,0,0,0.28);
  }
  /* Contact side */
  .card-contact {
    display: flex; align-items: center; justify-content: center;
    flex-direction: column; gap: 34px;
  }
  .contact-row { display: flex; align-items: center; gap: 18px; }
  .identity { text-align: right; }
  .identity-name {
    color: var(--accent); font-weight: 500; font-size: 17px; letter-spacing: 0.4px;
    text-transform: uppercase;
  }
  .identity-title { color: var(--ink-light); font-size: 14px; margin-top: 3px; }
  .divider { width: 1px; height: 64px; background: var(--rule); }
  .details { list-style: none; display: flex; flex-direction: column; gap: 5px; }
  .details li {
    display: flex; align-items: center; gap: 9px;
    color: var(--ink-light); font-size: 12.5px;
  }
  .details svg { width: 12px; height: 12px; flex: none; }
  .abn { color: var(--ink-light); font-size: 13px; letter-spacing: 0.3px; margin-left: 110px; }
  /* Brand side */
  .card-brand { display: flex; align-items: center; justify-content: center; gap: 14px; }
  .brand-dot { width: 22px; height: 22px; border-radius: 50%; background: var(--accent); }
  .brand-name {
    color: var(--ink-light); font-weight: 500; font-size: 30px; letter-spacing: 1px;
  }
</style>
</head>
<body>
<main class="stage">
  <section class="card card-contact" aria-label="Business card, contact side">
    <div class="contact-row">
      <div class="identity">
        <p class="identity-name">Rowan Keddle</p>
        <p class="identity-title">Director</p>
      </div>
      <span class="divider"></span>
      <ul class="details">
        <li>
          <svg viewBox="0 0 24 24" aria-hidden="true"><path fill="#0aa6e6" d="M6.6 10.8a15.1 15.1 0 0 0 6.6 6.6l2.2-2.2c.3-.3.7-.4 1-.2 1.1.4 2.3.6 3.6.6.6 0 1 .4 1 1V20c0 .6-.4 1-1 1A17 17 0 0 1 3 4c0-.6.4-1 1-1h3.5c.6 0 1 .4 1 1 0 1.3.2 2.5.6 3.6.1.3 0 .7-.2 1z"/></svg>
          0431 286 517
        </li>
        <li>
          <svg viewBox="0 0 24 24" aria-hidden="true"><rect x="2" y="5" width="20" height="14" fill="#0aa6e6"/><path d="M2 5l10 8 10-8" fill="none" stroke="#1e232a" stroke-width="2"/></svg>
          rowan@tbk-plumbing.com.au
        </li>
        <li>
          <svg viewBox="0 0 24 24" aria-hidden="true"><g fill="none" stroke="#0aa6e6" stroke-width="2"><circle cx="12" cy="12" r="9"/><ellipse cx="12" cy="12" rx="4" ry="9"/><path d="M3 12h18M5 7h14M5 17h14"/></g></svg>
          tbk-plumbing.com.au
        </li>
      </ul>
    </div>
    <p class="abn">ABN - 73 215 904 386</p>
  </section>

  <section class="card card-brand" aria-label="Business card, brand side">
    <span class="brand-name">TBK Plumbing Services</span>
    <span class="brand-dot" aria-hidden="true"></span>
  </section>
</main>
</body>
</html>
```